Local Roofing/Construction company business needs new biz card design

We need a new business card design, current cards are from the start of this operation and generic at best. We are a local Construction Company (General Contractor) with a majority of our work originating from insurance claims-exterior finish work is the main focus (Roofs-Siding-Gutters etc). Heavily involved with homeowners and the low ball offers they receive from insurance company's after a insurable event takes place. I have attached some of our original logo file(s) below.

```html
<!DOCTYPE html>
<html lang="en">
<head>
<meta charset="utf-8">
<title>Ironline Construction – Business Card</title>
<link href="https://fonts.googleapis.com/css2?family=Montserrat:wght@600;700;800&family=Lato:wght@400;700&display=swap" rel="stylesheet">
<style>
  :root {
    --bg: #c9c9c9;
    --card: #0e1d21;
    --card-deep: #0a1619;
    --pattern-a: #13282d;
    --pattern-b: #0c1b1f;
    --green: #4cb86c;
    --white: #f2f4f3;
  }
  * { box-sizing: border-box; margin: 0; padding: 0; }
  html, body { width: 1200px; height: 788px; overflow: hidden; }
  body {
    background: var(--bg);
    font-family: "Lato", sans-serif;
    position: relative;
  }
  .card {
    position: absolute;
    top: 244px;
    width: 525px;
    height: 300px;
    border-radius: 18px;
    background: var(--card);
    overflow: hidden;
    box-shadow: 0 14px 30px rgba(0,0,0,0.28);
  }
  .card--front { left: 50px; }
  .card--back { left: 625px; }

  /* Front */
  .person {
    position: absolute;
    right: 36px;
    top: 34px;
    text-align: right;
  }
  .person__name {
    font-family: "Montserrat", sans-serif;
    font-weight: 700;
    font-size: 21px;
    letter-spacing: 1.5px;
    color: var(--green);
    white-space: nowrap;
  }
  .person__title {
    font-size: 13px;
    color: var(--white);
    margin-top: 4px;
    letter-spacing: 0.5px;
  }
  .brand-badge {
    position: absolute;
    left: 34px;
    top: 108px;
    display: flex;
    align-items: center;
    gap: 10px;
    background: var(--green);
    border-radius: 9px;
    padding: 10px 16px;
    white-space: nowrap;
  }
  .brand-badge__square {
    width: 18px; height: 18px;
    background: var(--card);
    border-radius: 3px;
    flex: none;
  }
  .brand-badge__name {
    font-family: "Montserrat", sans-serif;
    font-weight: 800;
    font-size: 14px;
    letter-spacing: 1px;
    color: var(--card);
    text-transform: uppercase;
    line-height: 1;
  }
  .address {
    position: absolute;
    left: 38px;
    top: 164px;
    font-size: 13.5px;
    line-height: 1.45;
    color: var(--white);
    letter-spacing: 0.4px;
  }
  .contact {
    position: absolute;
    left: 38px;
    top: 214px;
    list-style: none;
    font-size: 13.5px;
    color: var(--white);
    letter-spacing: 0.4px;
  }
  .contact li {
    display: flex;
    align-items: center;
    gap: 9px;
    line-height: 1.5;
  }
  .contact svg { width: 12px; height: 12px; flex: none; }
  .green-band {
    position: absolute;
    left: 0; right: 0; bottom: 0;
    height: 8px;
    background: var(--green);
  }

  /* Back */
  .brand-pattern {
    position: absolute;
    inset: 0;
    background: linear-gradient(135deg, var(--pattern-a) 0%, var(--pattern-b) 70%, var(--card-deep) 100%);
  }
  .back-mark {
    position: absolute;
    right: 44px;
    bottom: 78px;
    display: flex;
    align-items: center;
    gap: 7px;
  }
  .back-mark__square {
    width: 14px; height: 14px;
    border-radius: 2px;
    background: var(--green);
  }
  .back-mark__name {
    font-family: "Montserrat", sans-serif;
    font-weight: 800;
    font-size: 12px;
    letter-spacing: 0.8px;
    color: var(--green);
    text-transform: uppercase;
  }
</style>
</head>
<body>
  <section class="card card--front">
    <div class="person">
      <p class="person__name">DYLAN MARSH</p>
      <p class="person__title">Managing Director</p>
    </div>

    <div class="brand-badge">
      <span class="brand-badge__square"></span>
      <span class="brand-badge__name">Ironline Construction</span>
    </div>

    <p class="address">415 W Cedar Avenue<br>Harlow County Name 7420</p>

    <ul class="contact">
      <li>
        <svg viewBox="0 0 12 12" aria-hidden="true"><circle cx="6" cy="6" r="6" fill="var(--green)"/><path d="M3.6 3.2l1.1-.3.6 1.4-.7.5c.3.7.9 1.3 1.6 1.6l.5-.7 1.4.6-.3 1.1C5.7 7.6 4.4 6.3 3.6 3.2z" fill="var(--card)"/></svg>
        0412 555 019
      </li>
      <li>
        <svg viewBox="0 0 12 12" aria-hidden="true"><circle cx="6" cy="6" r="6" fill="var(--green)"/><rect x="3" y="4" width="6" height="4.2" fill="none" stroke="var(--card)" stroke-width="0.9"/><path d="M3 4l3 2.3L9 4" fill="none" stroke="var(--card)" stroke-width="0.9"/></svg>
        info@ironlinebuild.com
      </li>
      <li>
        <svg viewBox="0 0 12 12" aria-hidden="true"><circle cx="6" cy="6" r="6" fill="var(--green)"/><circle cx="6" cy="6" r="3.2" fill="none" stroke="var(--card)" stroke-width="0.8"/><path d="M2.8 6h6.4M6 2.8c-1.4 1.8-1.4 4.6 0 6.4M6 2.8c1.4 1.8 1.4 4.6 0 6.4" fill="none" stroke="var(--card)" stroke-width="0.7"/></svg>
        www.ironlinebuild.com
      </li>
    </ul>

    <div class="green-band"></div>
  </section>

  <section class="card card--back">
    <div class="brand-pattern" role="img" aria-label="Repeating tonal pattern of the company brand mark across the card back"></div>
    <div class="back-mark">
      <span class="back-mark__square"></span>
      <span class="back-mark__name">Ironline</span>
    </div>
  </section>
</body>
</html>
```